Brightcoat Painting Services Requires a New Responsive Site

Hi Designers,

Our current website is this www.brightcoatpainting.com.au for some idea.
I made it on Adobe Muse, its very basic.
I would like it to be redesigned to look more professional and also responsive. I actually know how to do html5 and css but I think others will do this much better than me.

I do not need content because I am a copywriter and would like to do all SEO and copy myself.

The most improtant things to remember is that the site cannot use a CMS
and the code needs to be understandable so that I can go in and add content later on and do SEO work.

Also the site requires an additional testimonial page. I would imagine a nice gallery would be a great addition too(something that I can add images too through html. Also in it is important for it to contain those brand images on the front page as it increases authority. I will attach them onto the brief.

Those two files of nearbyfind and tradeleafs are local directories where we have reviews so a placement of those on the testimonail page would make great sense. I will to the href myself.

Anyway, good luck!

I look forward to see your designs :D
Updates

I have just been informed that on this site websites are simply designed and not built (developed) if this is the case please stop working on your designs and spending more time on this project. I REQUIRE DEVELOPMENT ALSO AND HAVE ALREADY CONTACTED SUPPORT.

Target Market(s)

The target market is 30-75 high income earners.

Industry/Entity Type

Painting

Number of Pages Required

5+ page

Font styles to use
Serif
Sans Serif

Requirements
Must have
• attractive gallery, and the brand icons uploaded.
• must be responsive
• web carousel (with the different types of work we do). eg domestic, commercial, industrial etc.
Nice to have
• a little interactivity
• corporate a natural design that goes well with our logo
Should not have
• any content. just write jiberish to fill in the spaces.
• I will be doing all copy and SEO myself.
• More than five pages, bascially the four that already exist plus the testimonail one.

```html
<!DOCTYPE html>
<html lang="en">
<head>
<meta charset="utf-8">
<title>Brightcoat Painting Services</title>
<link rel="stylesheet" href="https://fonts.googleapis.com/css2?family=Source+Sans+3:wght@400;600;700&display=swap">
<style>
  :root{
    --ink:#3f3f3f;
    --ink-soft:#555;
    --white:#ffffff;
    --footer:#2d2d2d;
    --tan-light:#e9cfa0;
    --tan:#c9a06a;
    --tan-dark:#6b4a2c;
    --sofa:#e07a24;
    --panel:rgba(240,236,232,.72);
    --brand-ink:#2a2a2a;
  }
  *{box-sizing:border-box;margin:0;padding:0}
  html,body{width:1200px;height:1116px;overflow:hidden;background:var(--white)}
  body{position:relative;font-family:"Source Sans 3",Arial,sans-serif;color:var(--ink)}

  .hero{position:absolute;left:0;top:0;width:1200px;height:630px;overflow:hidden}
  .hero-photo{position:absolute;inset:0;
    background:
      radial-gradient(ellipse 520px 260px at 440px 450px,var(--sofa) 0%,rgba(224,122,36,.85) 45%,rgba(224,122,36,0) 100%),
      radial-gradient(ellipse 900px 600px at 1050px 120px,#f3dcae 0%,rgba(243,220,174,0) 70%),
      linear-gradient(90deg,var(--tan-dark) 0%,var(--tan) 35%,var(--tan-light) 100%);}
  .hero-strip{position:absolute;left:0;right:0;bottom:0;height:28px;background:rgba(255,255,255,.55)}

  .brand{position:absolute;left:60px;top:22px}
  .brand-mark{width:70px;height:70px;background:#5a98c6;display:block;margin-bottom:98px}
  .brand-name{position:absolute;left:2px;top:175px;white-space:nowrap;font-size:19px;font-weight:700;letter-spacing:.5px;color:#4a4a4a}

  .main-nav{position:absolute;top:60px;right:59px;display:flex;gap:0}
  .main-nav a{display:flex;align-items:center;font-size:13px;color:var(--ink);text-decoration:none;letter-spacing:.3px;margin-left:40px}
  .main-nav a::before{content:"";width:7px;height:7px;background:#3a3a3a;margin-right:11px}
  .main-nav a.active{color:var(--white)}
  .main-nav a.active::before{background:var(--white)}
  .main-nav a:first-child{margin-left:0}

  .slide-title{position:absolute;left:57px;top:278px;font-size:66px;font-weight:700;color:var(--white);line-height:1;letter-spacing:-.5px}
  .slide-text{position:absolute;left:62px;top:346px;width:390px;font-size:17.5px;line-height:21px;color:var(--white);text-transform:uppercase}
  .slide-next{position:absolute;left:1103px;top:336px;width:36px;height:36px;border-radius:50%;background:#333;display:flex;align-items:center;justify-content:center}

  .service{position:absolute;background:var(--panel);text-align:center}
  .service h2{font-size:19px;font-weight:700;letter-spacing:.5px;color:var(--ink)}
  .service-heritage{left:798px;top:423px;width:342px;height:207px;padding-top:24px}
  .service-heritage p{margin:26px auto 0;width:270px;font-size:15px;line-height:22px;color:var(--ink-soft)}
  .service-commercial{left:60px;top:566px;width:342px;height:64px;padding-top:21px}
  .service-industrial{left:429px;top:566px;width:342px;height:64px;padding-top:21px}

  .gallery{position:absolute;left:60px;top:630px;width:1080px;height:182px;background:var(--white);
    box-shadow:0 6px 10px rgba(0,0,0,.12);border-radius:0 0 4px 4px;background:linear-gradient(#fff 80%,#efefef)}
  .thumb{position:absolute;top:18px;width:161px;height:138px}
  .t1{left:25px;background:linear-gradient(90deg,#f0b70c,#f7d13a)}
  .t2{left:198px;background:linear-gradient(90deg,#f3c57a,#efe3b0 60%,#f3da5a)}
  .t3{left:371px;background:linear-gradient(#7cc04a,#5fa33a 80%,#e5752a)}
  .t4{left:546px;background:linear-gradient(90deg,#3e3532,#4b403b 70%,#e9e2d0)}
  .t5{left:721px;background:linear-gradient(90deg,#d6d8da,#8a8d90 50%,#e9793a)}
  .t6{left:893px;background:linear-gradient(#dcc7da,#e8d9e6 70%,#c23060)}

  .partners{position:absolute;left:0;top:840px;width:1200px;height:143px}
  .partner{position:absolute;top:0;height:143px;display:flex;align-items:center;justify-content:center;transform:translateX(-50%)}
  .partner-name{font-size:22px;font-weight:700;color:var(--brand-ink);white-space:nowrap}
  .badge{display:block}
  .badge-local{width:119px;height:119px;background:#1aa7e0}
  .badge-leafs{width:116px;height:125px;background:#f4ea1a;border:6px solid #111;border-radius:10px}
  .badge-warranty{width:108px;height:118px;background:#1b4f8a;border-radius:6px 6px 54px 54px}

  .site-footer{position:absolute;left:0;top:1005px;width:1200px;height:111px;background:var(--footer);color:var(--white)}
  .footer-nav a{position:absolute;top:40px;font-size:13px;color:var(--white);text-decoration:none}
  .copyright{position:absolute;left:60px;top:67px;font-size:11px}
  .social{position:absolute;right:60px;top:54px;display:flex;gap:12px}
  .social a{display:flex;align-items:center;font-size:11px;color:var(--white);text-decoration:none}
  .social a::before{content:"";width:12px;height:12px;border-radius:50%;background:var(--white);margin-right:5px}
</style>
</head>
<body>
  <header class="hero">
    <div class="hero-photo" role="img" aria-label="Warm beige living room with an orange sofa and three dark square wall shelves"></div>
    <div class="hero-strip"></div>

    <div class="brand">
      <span class="brand-mark"></span>
      <span class="brand-name">BRIGHTCOAT PAINTING</span>
    </div>

    <nav class="main-nav">
      <a class="active" href="#">HOME</a>
      <a href="#">SERVICES</a>
      <a href="#">GALLERY</a>
      <a href="#">CONTACT US</a>
    </nav>

    <h1 class="slide-title">DECORATING</h1>
    <p class="slide-text">We care about our clients&amp; can make their life easier!</p>
    <a class="slide-next" href="#" aria-label="Next slide">
      <svg width="14" height="18" viewBox="0 0 14 18"><path d="M4 2 L11 9 L4 16" fill="none" stroke="#fff" stroke-width="2.4"/></svg>
    </a>

    <section class="service service-heritage">
      <h2>HERITAGE PAINTING</h2>
      <p>We are committed to an unmatched attention to detail to ensure an outstanding result</p>
    </section>
    <section class="service service-commercial"><h2>COMMERCIAL PAINTING</h2></section>
    <section class="service service-industrial"><h2>INDUSTRIAL PAINTING</h2></section>
  </header>

  <section class="gallery">
    <div class="thumb t1" role="img" aria-label="White armchair against a yellow wall"></div>
    <div class="thumb t2" role="img" aria-label="Green sideboard with vases in a pastel room"></div>
    <div class="thumb t3" role="img" aria-label="Green wall with orange lounge and floor lamp"></div>
    <div class="thumb t4" role="img" aria-label="Dark brown wall with colourful art above a cream sofa"></div>
    <div class="thumb t5" role="img" aria-label="Grey office with orange cabinets and desks"></div>
    <div class="thumb t6" role="img" aria-label="White sofa in a lilac room on a striped rug"></div>
  </section>

  <section class="partners" aria-label="Partners and listings">
    <div class="partner" style="left:142px"><span class="partner-name">Durafinish</span></div>
    <div class="partner" style="left:349px"><span class="partner-name">Hollins Paint</span></div>
    <div class="partner" style="left:538px"><span class="partner-name">Tallow &amp; Co</span></div>
    <div class="partner" style="left:735px"><span class="badge badge-local" role="img" aria-label="nearbyfind listing badge"></span></div>
    <div class="partner" style="left:909px"><span class="badge badge-leafs" role="img" aria-label="tradeleafs listing badge"></span></div>
    <div class="partner" style="left:1082px"><span class="badge badge-warranty" role="img" aria-label="Five year workmanship warranty badge"></span></div>
  </section>

  <footer class="site-footer">
    <nav class="footer-nav">
      <a href="#" style="left:62px">Home</a>
      <a href="#" style="left:152px">Services</a>
      <a href="#" style="left:262px">Gallery</a>
      <a href="#" style="left:359px">Contact Us</a>
    </nav>
    <p class="copyright">© 2014 Brightcoat Painting All rights reserved.</p>
    <div class="social">
      <a href="#">Chirper</a>
      <a href="#">WorkNet</a>
      <a href="#">PlusOne</a>
      <a href="#">FaceSpace</a>
    </div>
  </footer>
</body>
</html>
```